Pebblewood Youth Games Club

I need a family friendly website for children's sports coaching, diets and the importance of children's nutrition, child minding services,children's councilling and physiology services.
Also once I have an understanding of numbers and my fees I will offer a pick up service for my classes

Please add my new logo which is my buisness name,

Target Market(s)

Children of all ages and parents who would like there kids involved in sporting programmes ,

Industry/Entity Type

Nutrition

Requirements
Must have
• Active kids are healthy kids..
Also the logo I have uploaded .
Skype and video calls available for parents to see child's progress and safety at classes if parents are unable to attend.
Nice to have
• Listed about the services I will be offering,
One on one and group sessions.child minding and nanny services, parent and child councilling and physcology services,diet and nutrition personalisation services,pick up services,school visits and motivational classes,
Fully covered and insured business,

```html
<!DOCTYPE html>
<html lang="en">
<head>
<meta charset="utf-8">
<title>Pebblewood Youth Games Club</title>
<link href="https://fonts.googleapis.com/css2?family=Open+Sans:wght@400;600;700&family=Oswald:wght@500&display=swap" rel="stylesheet">
<style>
:root{
  --page:#f4f4f2;
  --blue:#2a8fd6;
  --blue-light:#45a9ea;
  --blue-dark:#1c78c0;
  --ink:#1a1a1a;
  --text:#3a3a3a;
  --green-dark:#4f8f18;
  --card:#ffffff;
  --line:#d9d9d9;
  --red:#e01616;
}
*{box-sizing:border-box;margin:0;padding:0}
html,body{width:1154px;height:1200px;overflow:hidden}
body{background:var(--page);font-family:"Open Sans",Arial,sans-serif;color:var(--text);position:relative}
.abs{position:absolute}
.brand{left:92px;top:30px;display:flex;align-items:center;gap:10px;width:210px}
.brand-dot{width:34px;height:34px;border-radius:50%;background:var(--blue);flex:none}
.brand-name{font-weight:700;font-size:17px;line-height:21px;color:var(--blue)}
.partner-name{left:307px;top:26px;width:90px;font-weight:700;font-size:15px;line-height:19px;color:var(--red);text-align:center}
.social{right:90px;top:14px;display:flex;gap:9px}
.social span{width:28px;height:28px;border-radius:50%;background:var(--blue-dark);display:block}
.phone{left:903px;top:50px;display:flex;align-items:center;gap:6px;font-family:"Oswald",sans-serif;font-weight:500;font-size:23px;color:var(--blue);white-space:nowrap}
.main-nav{left:305px;top:93px;width:759px;height:35px;background:linear-gradient(var(--blue-light),var(--blue-dark));border-radius:3px;display:flex;white-space:nowrap;overflow:hidden}
.main-nav a{color:#fff;text-decoration:none;font-size:14px;line-height:35px;padding:0 12px;border-right:1px solid rgba(255,255,255,.35);white-space:nowrap}
.main-nav a:first-child{padding-left:17px}
.main-nav a:last-child{border:none}
.hero{left:97px;top:147px;width:961px;height:336px}
.arrow{width:42px;height:42px;border-radius:50%;background:#fff;box-shadow:0 1px 4px rgba(0,0,0,.35);display:flex;align-items:center;justify-content:center;top:262px}
.card{top:506px;width:185px;height:267px;background:var(--card);box-shadow:0 1px 4px rgba(0,0,0,.18);border-radius:3px;padding:16px 16px 0 17px}
.card h2{font-size:18.5px;line-height:21px;font-weight:700;color:var(--ink);margin-bottom:5px}
.card p{font-size:11.4px;line-height:19.4px;text-align:justify}
.btn-detail{position:absolute;left:17px;top:230px;width:69px;height:28px;background:linear-gradient(#86c83c,var(--green-dark));border-radius:3px;color:#fff;font-weight:700;font-size:12px;line-height:28px;text-align:center}
.card-art{position:absolute;right:6px;bottom:3px;width:86px;height:50px;border-radius:4px}
.join-title{font-size:19px;font-weight:700;color:var(--blue);line-height:22px}
.join-sub{font-size:12px;font-weight:700;color:var(--blue);margin-bottom:8px}
.join-list{list-style:none;font-size:12px;color:var(--ink);line-height:24px}
.btn-join{position:absolute;left:18px;top:230px;width:92px;height:30px;background:linear-gradient(#ff3a3a,#cc0000);border-radius:3px;color:#fff;font-weight:700;font-size:12px;line-height:30px;text-align:center}
.welcome{left:92px;top:790px;width:722px}
.welcome h1{font-size:23px;font-weight:700;color:var(--ink);margin-bottom:6px;white-space:nowrap}
.welcome h1 span{color:var(--blue)}
.welcome p{font-size:11.6px;line-height:21.2px;color:var(--ink);margin-left:2px;margin-bottom:21px;letter-spacing:-.1px}
.welcome a{font-size:12px;color:var(--blue);text-decoration:none;border-bottom:1px solid var(--blue);margin-left:2px}
.enquiry{left:840px;top:796px;width:223px;height:293px;background:var(--card);border-radius:3px;box-shadow:0 1px 4px rgba(0,0,0,.18);padding:14px 20px}
.enquiry h2{font-size:24px;font-weight:700;color:var(--ink);margin-bottom:10px;white-space:nowrap}
.field{height:29px;border:1px solid var(--line);border-radius:2px;font-size:11px;color:#777;padding:0 12px;line-height:27px;margin-bottom:10px;position:relative}
.field.select::after{content:"";position:absolute;right:10px;top:10px;border:5px solid transparent;border-top:8px solid #777}
.field.msg{height:68px;line-height:16px;padding-top:8px}
.btn-go{position:absolute;right:10px;top:18px;width:38px;height:38px;border-radius:50%;background:radial-gradient(circle at 40% 35%,#ff4a4a,#c80000);color:#fff;font-weight:700;font-size:15px;line-height:38px;text-align:center}
.footer-nav{left:91px;top:1108px;width:973px;height:34px;background:linear-gradient(var(--blue-light),var(--blue-dark));border-radius:3px;display:flex;justify-content:center;align-items:center;color:#fff;font-size:12.5px;white-space:nowrap}
.footer-nav a{color:#fff;text-decoration:none;padding:0 11px}
.legal{left:0;width:1154px;top:1156px;text-align:center;font-size:11.5px;color:#444;line-height:18px}
</style>
</head>
<body>

<div class="abs brand"><span class="brand-dot"></span><span class="brand-name">Pebblewood Youth Games Club</span></div>
<div class="abs partner-name">Kindness Circle</div>

<div class="abs social" aria-label="Social links"><span></span><span></span><span></span></div>

<div class="abs phone">
  <svg width="20" height="30" viewBox="0 0 20 30"><rect x="1.5" y="1.5" width="17" height="27" rx="3" fill="none" stroke="currentColor" stroke-width="3"/><rect x="5" y="5" width="10" height="17" fill="currentColor"/></svg>
  25645 880 4120
</div>

<nav class="abs main-nav">
  <a href="#">HOME</a><a href="#">ABOUT US</a><a href="#">ACTIVITIES</a><a href="#">NEWS</a><a href="#">PARTNERS</a><a href="#">CAREER OPPORTUNITIES</a><a href="#">CONTACT US</a>
</nav>

<svg class="abs hero" viewBox="0 0 961 336" role="img" aria-label="Photo of young children playing football on a grass pitch">
  <defs>
    <linearGradient id="pitch" x1="0" y1="0" x2="0" y2="1">
      <stop offset="0" stop-color="#8b9c62"/><stop offset=".5" stop-color="#7d9548"/><stop offset="1" stop-color="#6a8a3c"/>
    </linearGradient>
  </defs>
  <path d="M0 0H961V300Q480 390 0 300Z" fill="url(#pitch)"/>
  <path d="M0 300Q480 390 961 300" fill="none" stroke="#fff" stroke-width="5"/>
</svg>
<div class="abs arrow" style="left:78px"><svg width="26" height="26" viewBox="0 0 26 26"><circle cx="13" cy="13" r="13" fill="var(--blue-dark)"/><path d="M20 13H8M13 7L7 13L13 19" stroke="#fff" stroke-width="3" fill="none"/></svg></div>
<div class="abs arrow" style="left:1037px"><svg width="26" height="26" viewBox="0 0 26 26"><circle cx="13" cy="13" r="13" fill="var(--blue-dark)"/><path d="M6 13H18M13 7L19 13L13 19" stroke="#fff" stroke-width="3" fill="none"/></svg></div>

<article class="abs card" style="left:91px">
  <h2>NUTRITION FOR CHILDREN</h2>
  <p>Lorem Ipsum is simply dummy text of the printing and typesetting industry. Lorem Ipsum has been the industry's standard dummy text ever since the 1500s, when an unknown.</p>
  <span class="btn-detail">DETAIL</span>
  <div class="card-art" style="background:linear-gradient(#f4ddc8,#e0a070)" role="img" aria-label="Illustration of children eating healthy food"></div>
</article>
<article class="abs card" style="left:289px">
  <h2>CHILD MINDING SERVICE</h2>
  <p>Lorem Ipsum is simply dummy text of the printing and typesetting industry. Lorem Ipsum has been the industry's standard dummy text ever since the 1500s, when an unknown.</p>
  <span class="btn-detail">DETAIL</span>
  <div class="card-art" style="width:90px;background:linear-gradient(#f6d6c8,#e88070)" role="img" aria-label="Photo of smiling children lying in a row"></div>
</article>
<article class="abs card" style="left:485px">
  <h2>COACHING SERVICES</h2>
  <p>Lorem Ipsum is simply dummy text of the printing and typesetting industry. Lorem Ipsum has been the industry's standard dummy text ever since the 1500s, when an unknown.</p>
  <span class="btn-detail" style="left:20px">DETAIL</span>
  <div class="card-art" style="background:linear-gradient(#f4e8e0,#7fa6c8)" role="img" aria-label="Photo of a coach stretching with a child"></div>
</article>
<article class="abs card" style="left:683px">
  <h2>PICK UP SERVICE</h2>
  <p>Lorem Ipsum is simply dummy text of the printing and typesetting industry. Lorem Ipsum has been the industry's standard dummy text ever since the 1500s, when an unknown.</p>
  <span class="btn-detail">DETAIL</span>
  <div class="card-art" style="height:40px;bottom:10px;background:linear-gradient(#ffffff,#c8ccd0)" role="img" aria-label="Image of a white minibus"></div>
</article>
<article class="abs card" style="left:880px">
  <h2>CHILDREN'S COUNCILLING</h2>
  <div class="join-title" style="margin-top:10px">Free to join,</div>
  <div class="join-sub">loads of benefits!</div>
  <ul class="join-list"><li>holiday courses</li><li>SMS alerts</li><li>holiday courses</li><li>SMS alerts</li></ul>
  <span class="btn-join">JOIN NOW</span>
  <div class="card-art" style="width:44px;height:88px;right:5px;background:linear-gradient(#f0e6b0,#3f7fc0)" role="img" aria-label="Photo of two children running"></div>
</article>

<section class="abs welcome">
  <h1>WELCOME TO <span>PEBBLEWOOD YOUTH GAMES CLUB</span></h1>
  <p>Lorem Ipsum is simply dummy text of the printing and typesetting industry. Lorem Ipsum has been the industry's standard dummy text ever since the 1500s, when an unknown printer took a galley of type and scrambled it to make a type specimen book. It has survived not only five centuries, but also the leap into electronic typesetting, remaining essentially unchanged. It was popularised in the 1960s with the release of Letraset sheets containing Lorem Ipsum passages, and more recently with desktop publishing software like Aldus PageMaker including versions of Lorem Ipsum.</p>
  <p style="margin-bottom:2px">Lorem Ipsum is simply dummy text of the printing and typesetting industry. Lorem Ipsum has been the industry's standard dummy text ever since the 1500s, when an unknown printer took a galley of type and scrambled it to make a type specimen book. It has survived not only five centuries, but also the leap into electronic typesetting, remaining essentially unchanged.</p>
  <a href="#">Know more</a>
</section>

<form class="abs enquiry">
  <h2>ENQUIRE NOW</h2>
  <div class="field">Name</div>
  <div class="field">Phone Number</div>
  <div class="field">Email Address</div>
  <div class="field select">Age</div>
  <div class="field msg">Message<span class="btn-go">GO</span></div>
</form>

<nav class="abs footer-nav">
  <a href="#">HOME</a>|<a href="#">ABOUT US</a>|<a href="#">ACTIVITIES</a>|<a href="#">NEWS</a>|<a href="#">PARTNERS</a>|<a href="#">CAREER OPPORTUNITIES</a>|<a href="#">CONTACT US</a>
</nav>

<footer class="abs legal">
  Privacy Policy &nbsp;|&nbsp; Legal Notice &nbsp;|&nbsp; Copyright &nbsp;|&nbsp; Sitemap<br>
  Copyright © 2014 pebblewoodyouthgames.com. All Rights Reserved.
</footer>

</body>
</html>
```